Business Card Design - Photographer

I am a landscape photographer and I require a business card design. 

I require two designs:
1)  a double sided business card
 and
b)  a single sided business card 

The single sided design can either be the same as the double sided (with just one side having all the information)....or it can be an entire new design. Its up to you.

My corporate colours are (CMYK):

Blue   69, 32, 0, 0
Grey  72,  64,  47,  31
Green  32,  2,  91,  0
Yellow   0, 19, 92, 0
Orange  0, 39, 75, 0

Colour space in final file should be in CMYK.

The details that need to be included on the card:

- Use the provided Logo
- Name: Wiktor Baranowski
- Email:   sales@vistalumeworks.com.au
- Website:    vistalumeworks.com.au
- Twitter:    twitter.com/vistalumeworks
- Facebook:   facebook.com/vistalumeworks
- Mobile  0417 539 662

Please use the attached template to design the logo to the specified size, including the marked bleed lines. I have also attached my logo in PNG (transparent background) and ai format for you to use.

The final file should be:
- Photoshop version with layers so I can edit the name/text etc. All non vector files should be high resolution at 1039 x 697 pixels at 300 dpi.

I also require a file as:
- Vector based PDF

Anyway questions please contact me.

Thank you

Industry/Entity Type

Landscape

Logo styles of interest
Pictorial/Combination Logo
Abstract Logo
Wordmark Logo
Lettermark Logo
Requirements
Must have
• The details that need to be included on the card:

- Use the provided Logo
- Name: Wiktor Baranowski
- Email: sales@vistalumeworks.com.au
- Website: vistalumeworks.com.au
- Twitter: twitter.com/vistalumeworks
- Facebook: facebook.com/vistalumeworks
- Mobile 0417 539 662

```html
<!DOCTYPE html>
<html lang="en">
<head>
<meta charset="utf-8">
<title>Wiktor Baranowski – Business Cards</title>
<link rel="stylesheet" href="https://fonts.googleapis.com/css2?family=Cinzel:wght@500&family=Arimo:wght@400&display=swap">
<style>
  :root {
    --page-bg: #a8832a;
    --card-bg: #ffffff;
    --ink-grey: #3d4150;
    --ink-dark: #23252f;
    --text-body: #2a2a2a;
    --brand-blue: #3d94d0;
    --blue-deep: #2d72a8;
    --yellow: #fcc419;
    --yellow-deep: #d9b10a;
    --orange-light: #f6a95a;
    --orange: #f48c1e;
    --green-light: #b7d43c;
    --green: #9bb12b;
    --divider: #9a9a9a;
  }
  * { margin: 0; padding: 0; box-sizing: border-box; }
  html, body { width: 1200px; height: 686px; overflow: hidden; }
  body { background: var(--page-bg); position: relative; font-family: "Arimo", Arial, sans-serif; }

  .card {
    position: absolute;
    width: 524px;
    height: 300px;
    background: var(--card-bg);
    box-shadow: 2px 3px 6px rgba(0,0,0,0.3);
    overflow: hidden;
  }
  .card--front { left: 50px; top: 147px; }
  .card--back  { left: 614px; top: 260px; }

  .color-strip { position: absolute; display: flex; }
  .color-strip span { flex: 1; }
  .card--front .color-strip { left: 0; right: 0; bottom: 0; height: 12px; flex-direction: row; }
  .card--back .color-strip  { top: 0; bottom: 0; right: 0; width: 12px; flex-direction: column; }
  .s1 { background: var(--yellow); } .s2 { background: var(--yellow-deep); }
  .s3 { background: var(--orange-light); } .s4 { background: var(--orange); }
  .s5 { background: var(--green-light); } .s6 { background: var(--green); }
  .s7 { background: var(--brand-blue); } .s8 { background: var(--blue-deep); }
  .s9 { background: var(--ink-grey); } .s10 { background: var(--ink-dark); }

  .brand { position: absolute; top: 0; height: 100%; }
  .brand > * { position: absolute; left: 50%; transform: translateX(-50%); }
  .brand-mark { border-radius: 50%; background: var(--ink-grey); }
  .brand-name {
    font-family: "Cinzel", "Times New Roman", serif;
    font-weight: 500;
    color: var(--ink-grey);
    white-space: nowrap;
    text-align: center;
  }
  .brand-rule { height: 1px; background: var(--ink-grey); }
  .brand-tagline {
    font-family: "Cinzel", "Times New Roman", serif;
    font-weight: 500;
    color: var(--ink-grey);
    white-space: nowrap;
    text-align: center;
  }

  .card--front .brand { left: 19px; width: 240px; }
  .card--front .brand-mark { top: 76px; width: 84px; height: 84px; }
  .card--front .brand-name { top: 171px; font-size: 20px; line-height: 24px; letter-spacing: 0.3px; }
  .card--front .brand-rule { top: 196px; width: 227px; }
  .card--front .brand-tagline { top: 200px; font-size: 10px; line-height: 13px; letter-spacing: 1.6px; }

  .divider { position: absolute; left: 273px; top: 80px; width: 1px; height: 133px; background: var(--divider); }

  .contact { position: absolute; left: 297px; top: 75px; font-size: 13px; color: var(--text-body); list-style: none; }
  .contact li { display: flex; align-items: center; height: 19px; }
  .contact svg { width: 12px; height: 12px; margin-right: 6px; flex: none; }
  .contact .gap { margin-top: 8px; }
  .social-box { width: 12px; height: 12px; margin-right: 6px; flex: none; }
  .social-box--a { background: var(--brand-blue); }
  .social-box--b { background: var(--blue-deep); }
  .address { position: absolute; left: 297px; top: 192px; font-size: 13px; line-height: 16px; color: var(--text-body); }

  .card--back .brand { left: 0; width: 500px; }
  .card--back .brand-mark { top: 36px; width: 111px; height: 111px; }
  .card--back .brand-name { top: 168px; font-size: 26px; line-height: 30px; letter-spacing: 0.6px; }
  .card--back .brand-rule { top: 200px; width: 297px; }
  .card--back .brand-tagline { top: 206px; font-size: 12px; line-height: 15px; letter-spacing: 2.4px; }
  .web-line { position: absolute; left: 0; width: 500px; top: 240px; text-align: center; font-size: 13px; color: var(--ink-grey); }
  .web-line .web-name { font-family: "Cinzel", "Times New Roman", serif; font-size: 14px; color: var(--brand-blue); }
</style>
</head>
<body>

<section class="card card--front" aria-label="Business card front">
  <div class="brand">
    <span class="brand-mark"></span>
    <div class="brand-name">Wiktor Baranowski</div>
    <div class="brand-rule"></div>
    <div class="brand-tagline">Fine Art Photography</div>
  </div>
  <div class="divider"></div>
  <ul class="contact">
    <li>
      <svg viewBox="0 0 12 12"><path d="M2.5 1 L4.5 1 L5 3.5 L3.8 4.5 Q5 7 7.5 8.2 L8.5 7 L11 7.5 L11 9.5 Q10.5 11 9 11 Q4 10.5 1 3 Q1 1.5 2.5 1Z" fill="var(--brand-blue)"/></svg>
      0417 539 662
    </li>
    <li>
      <svg viewBox="0 0 12 12"><rect x="0.5" y="2.5" width="11" height="7" fill="var(--brand-blue)"/><path d="M0.5 2.5 L6 7 L11.5 2.5" fill="none" stroke="#fff" stroke-width="1"/></svg>
      sales@vistalumeworks.com.au
    </li>
    <li>
      <svg viewBox="0 0 12 12"><circle cx="6" cy="6" r="5.2" fill="var(--brand-blue)"/><g fill="none" stroke="#fff" stroke-width="0.7"><ellipse cx="6" cy="6" rx="2.2" ry="5.2"/><line x1="0.8" y1="6" x2="11.2" y2="6"/><line x1="1.8" y1="3.5" x2="10.2" y2="3.5"/><line x1="1.8" y1="8.5" x2="10.2" y2="8.5"/></g></svg>
      www.vistalumeworks.com.au
    </li>
    <li class="gap"><span class="social-box social-box--a"></span>@vistalumeworks</li>
    <li><span class="social-box social-box--b"></span>@vistalumeworks</li>
  </ul>
  <p class="address">Street name City<br>State, zip code</p>
  <div class="color-strip"><span class="s1"></span><span class="s2"></span><span class="s3"></span><span class="s4"></span><span class="s5"></span><span class="s6"></span><span class="s7"></span><span class="s8"></span><span class="s9"></span><span class="s10"></span></div>
</section>

<section class="card card--back" aria-label="Business card back">
  <div class="brand">
    <span class="brand-mark"></span>
    <div class="brand-name">Wiktor Baranowski</div>
    <div class="brand-rule"></div>
    <div class="brand-tagline">Fine Art Photography</div>
  </div>
  <p class="web-line">www. <span class="web-name">vistalumeworks</span> .com.au</p>
  <div class="color-strip"><span class="s1"></span><span class="s2"></span><span class="s3"></span><span class="s4"></span><span class="s5"></span><span class="s6"></span><span class="s7"></span><span class="s8"></span><span class="s9"></span><span class="s10"></span></div>
</section>

</body>
</html>
```